Counseling Practice Business Card

I need a professional looking business card incorporating my new logo that was just completed. Card needs to incorporate my name and title, description of my specialty, my address, my phone number, my fax number, my email and my website URL. I need to be able to choose design on/with different paper colors and textures.
I do not have a lot of business card ideas so I am open to anything but I want bold,sharp, clear card without additional designs other than my logo (see attached file info). I am open to different color backgrounds or paper colors including black. I do not like traditional brackets around area codes in phone number or dashes between numbers in phone number. Am open to other ways of presenting including periods between numbers as appropriate. I do not know enough to know what I like yet but I want card to coordinate and work together with my logo. My practice emphasizes natural mental health interventions so any use of color (with background paper color or the blue and green in my logo) that elicits nature is nice. In addition to black, any natural brown or wood looking background might be desirable also. Most of the offerings so far look very similar and boring.

Target Market(s)

Potential therapy clients and other professionals

Contact Information for Business Card

Card information:
Gerald M. Whitcombe, Ph.D.
Licensed Clinical Psychologist
Integrative Health Coach
4812 Marlowe Ridge Blvd SE
Suite 310
Duluth, GA 30096
(770) 415-2983 phone
(770) 581-4096 fax
drgeraldwhitcombe@quillmarsh.net
brightfernwellness.net

Font styles to use
Serif
Sans Serif
Other font styles liked:
• anything that you think looks crisp, clear and easily readable

Requirements
Must have
• Any color used should coordinate with my logo design (see attached files).
• Card should be printed horizontally so top and bottom are longest sides of rectangle.
• Background color or paper color should complement and highlight logo. Do not like a white background. black, grey, brown or any color my logo would blend well with.
Nice to have
• I would like designer to utilize color to highlight letters/name or phone-fax-web symbols.
• Bottom edge of card could be highlighted if appropriate to an idea.
Should not have
• I would NOT want the card to have a pure white background at all.
• No clear cards.
• Cards should be oriented with long sides on bottom and top, NOT sides. DO NOT LIKE THIS THIN TALL ORIENTATION.

```html
<!DOCTYPE html>
<html lang="en">
<head>
<meta charset="utf-8">
<title>Brightfern Wellness – Business Card</title>
<link href="https://fonts.googleapis.com/css2?family=Open+Sans:wght@400;600&display=swap" rel="stylesheet">
<style>
  :root {
    --stage: #d9dadc;
    --brand-blue: #2573b8;
    --brand-green: #006634;
    --ink: #3b3b3b;
    --paper: #f3f0e8;
    --front-text: #ffffff;
  }
  html, body {
    margin: 0;
    padding: 0;
    width: 1200px;
    height: 782px;
    overflow: hidden;
    background: var(--stage);
    font-family: "Open Sans", Arial, sans-serif;
  }
  .stage {
    position: relative;
    width: 1200px;
    height: 782px;
    display: flex;
    align-items: center;
    justify-content: center;
    gap: 40px;
  }
  .card {
    position: relative;
    width: 520px;
    height: 297px;
    overflow: hidden;
    box-shadow: 0 6px 18px rgba(0,0,0,0.18);
  }

  /* Front face */
  .card--front {
    background: var(--brand-blue);
    display: flex;
    align-items: center;
    justify-content: center;
  }
  .brand-name {
    font-weight: 600;
    line-height: 1;
    text-align: center;
  }
  .card--front .brand-name {
    color: var(--front-text);
    font-size: 46px;
  }

  /* Back face */
  .card--back {
    background: var(--paper);
    color: var(--ink);
  }
  .holder {
    position: absolute;
    left: 26px;
    top: 22px;
  }
  .holder__name {
    margin: 0;
    font-size: 15px;
    font-weight: 600;
    letter-spacing: 0.4px;
    text-transform: uppercase;
    color: var(--brand-blue);
  }
  .holder__name .degree { color: var(--brand-green); }
  .holder__title {
    margin: 3px 0 0;
    font-size: 12.5px;
    color: var(--ink);
  }
  .contact {
    position: absolute;
    left: 26px;
    top: 142px;
    margin: 0;
    padding: 0;
    list-style: none;
    font-size: 12.5px;
    line-height: 19px;
  }
  .contact li {
    display: flex;
    align-items: center;
    gap: 7px;
  }
  .contact svg {
    width: 11px;
    height: 11px;
    fill: var(--brand-blue);
    flex: none;
  }
  .card--back .brand-name {
    position: absolute;
    left: 300px;
    top: 120px;
    width: 190px;
    color: var(--brand-green);
    font-size: 30px;
  }
  .address {
    position: absolute;
    left: 322px;
    bottom: 44px;
    margin: 0;
    font-style: normal;
    font-size: 13px;
    line-height: 17px;
    text-align: left;
    color: var(--ink);
  }
  .edge-bands {
    position: absolute;
    left: 0;
    bottom: 0;
    width: 520px;
    height: 36px;
  }
</style>
</head>
<body>
<main class="stage">

  <section class="card card--front" aria-label="Card front">
    <div class="brand-name">Brightfern<br>Wellness</div>
  </section>

  <section class="card card--back" aria-label="Card back">
    <header class="holder">
      <h1 class="holder__name">Gerald M. Whitcombe, <span class="degree">Ph.D.</span></h1>
      <p class="holder__title">Licensed Clinical Psychologist / Integrative Health Coach</p>
    </header>

    <ul class="contact">
      <li>
        <svg viewBox="0 0 24 24" aria-hidden="true"><path d="M6.6 10.8a15.1 15.1 0 0 0 6.6 6.6l2.2-2.2c.3-.3.7-.4 1-.2 1.1.4 2.3.6 3.6.6.6 0 1 .4 1 1V20c0 .6-.4 1-1 1A17 17 0 0 1 3 4c0-.6.4-1 1-1h3.5c.6 0 1 .4 1 1 0 1.3.2 2.5.6 3.6.1.3 0 .7-.2 1z"/></svg>
        <span>770.415.2983</span>
      </li>
      <li>
        <svg viewBox="0 0 24 24" aria-hidden="true"><path d="M6 2h10v5H6zM3 8h18v10h-3v4H6v-4H3zm5 7v5h8v-5z"/></svg>
        <span>770.581.4096</span>
      </li>
      <li>
        <svg viewBox="0 0 24 24" aria-hidden="true"><path d="M2 5h20v14H2zm2 2v.5l8 5 8-5V7l-8 5z"/></svg>
        <span>drgeraldwhitcombe@quillmarsh.net</span>
      </li>
      <li>
        <svg viewBox="0 0 24 24" aria-hidden="true"><circle cx="12" cy="12" r="10"/></svg>
        <span>brightfernwellness.net</span>
      </li>
    </ul>

    <div class="brand-name">Brightfern<br>Wellness</div>

    <address class="address">
      4812 Marlowe Ridge Blvd SE<br>
      Suite 310 Duluth, GA 30096
    </address>

    <svg class="edge-bands" viewBox="0 0 520 36" aria-hidden="true">
      <polygon points="0,22 270,22 270,36 0,36" fill="var(--brand-blue)"/>
      <polygon points="282,8 520,8 520,36 270,36" fill="var(--brand-green)"/>
    </svg>
  </section>

</main>
</body>
</html>
```